Liron Vasek Website

Website for my son who is in 7th grade in the US. This will prepare him to show people his accomplishments when applying for a job or going to college. It should have:
* A picture (or multiple pictures)
* A resume page
* A place to share your accomplishments
* Links to his other social profiles
* A contact form

Great to include:
* Internships (show some photos of it along with what you’ve learned).
* Volunteer work.
* A side hustle that you want to highlight

Website sample I like:
https://belinamorud.sitefolio-demo.com/belinamorudtavik

Target Market(s)

For jobs and colleges admissions.

Number of Pages Required

5+ page

Colors

Designer to choose colors to be used in the design.

Requirements
Must have
• * A picture (or multiple pictures)
• * A resume page
• * A place to share your accomplishments
• * Links to his other social profiles
• * A contact form
Nice to have
• Great to include:
• * Internships (show some photos of it along with what you’ve learned).
• * Volunteer work.
• * A side hustle that you want to highlight

```html
<!DOCTYPE html>
<html lang="en">
<head>
<meta charset="utf-8">
<title>Liron Vasek</title>
<link rel="stylesheet" href="https://fonts.googleapis.com/css2?family=Domine:wght@400;500&family=Poppins:wght@400;500;600&family=Roboto:ital,wght@0,300;0,400;0,500;0,700;1,300&family=Roboto+Condensed:wght@700&display=swap">
<style>
:root{
  --teal:#0d5a63;
  --teal-dark:#0a4850;
  --ink:#1b1b1b;
  --muted:#777;
  --white:#fff;
  --night:#1d2125;
  --paper:#ededed;
  --gold:#f2b01e;
}
*{box-sizing:border-box;margin:0;padding:0}
html,body{width:1200px;height:4648px;overflow:hidden}
body{position:relative;background:var(--white);font-family:"Roboto",sans-serif;color:var(--ink)}
.abs{position:absolute}
.serif{font-family:"Domine",serif;font-weight:400}
svg{display:block}

.topbar{left:0;top:0;width:1200px;height:44px;background:var(--teal);color:var(--white);font-size:14px}
.topbar .contact-line{left:88px;top:13px;display:flex;gap:10px;align-items:center}
.topbar .social{right:88px;top:14px;display:flex;gap:12px}
.dot{width:15px;height:15px;border-radius:50%;background:rgba(255,255,255,.85)}

.logo{left:88px;top:100px;font-size:48px;color:var(--ink)}
.call{left:722px;top:87px;font-size:18px;font-weight:500;display:flex;align-items:center;gap:8px}
.call .ic{width:20px;height:20px;border-radius:50%;background:var(--teal)}
.btn-contact{left:969px;top:79px;width:134px;height:38px;border-radius:19px;background:var(--teal);color:var(--white);font-size:15px;font-weight:500;display:flex;align-items:center;justify-content:center}
.nav{top:160px;font-size:18px;font-weight:500}

.hero-photo{left:0;top:216px;width:1200px;height:760px;background:linear-gradient(100deg,#3c3a35 0%,#6c6152 40%,#a89986 70%,#7d6c5a 100%)}
.hero-shade{left:0;top:216px;width:700px;height:760px;background:linear-gradient(90deg,rgba(0,0,0,.45),rgba(0,0,0,0))}
.hero-kicker{left:88px;top:330px;font-size:44px;color:var(--white)}
.hero-title{left:88px;top:390px;font-size:66px;color:var(--white);font-weight:500}
.hero-text{left:88px;top:480px;width:410px;font-family:"Poppins",sans-serif;font-weight:500;font-size:15.5px;line-height:28px;color:var(--white)}
.btn-ghost{left:88px;top:624px;width:123px;height:42px;border:2px solid var(--white);border-radius:21px;color:var(--white);font-family:"Poppins",sans-serif;font-size:16px;font-weight:500;display:flex;align-items:center;justify-content:center}
.arrow{width:36px;height:36px;border-radius:50%;background:var(--teal);display:flex;align-items:center;justify-content:center}

.about-photo{left:114px;top:1075px;width:386px;height:386px;border-radius:50%;background:radial-gradient(circle at 50% 45%,#c9848f 0%,#8a8c94 55%,#5a5d66 100%)}
.about-title{left:605px;top:1058px;font-size:46px}
.about-text{left:605px;top:1124px;width:475px;font-size:16px;line-height:29.6px;color:var(--muted);font-weight:300}
.btn-solid{background:var(--teal);color:var(--white);border-radius:28px;display:flex;align-items:center;justify-content:center;font-weight:500}

.dark-band{left:0;top:1560px;width:1200px;height:1020px;background:radial-gradient(ellipse at 60% 40%,#2e3338 0%,#1d2125 60%,#15181b 100%)}
.card{top:1866px;width:332px;height:402px;background:var(--white);text-align:center}
.card .ph{position:absolute;left:9px;top:9px;width:314px;height:189px}
.card h3{position:absolute;left:0;right:0;top:228px;font-family:"Roboto Condensed",sans-serif;font-weight:700;font-size:29px;letter-spacing:.3px}
.card p{position:absolute;left:18px;right:18px;top:278px;font-size:15.5px;line-height:31px;color:var(--muted);font-weight:300}

.section-title{left:0;width:1200px;text-align:center;font-size:46px}
.quote-back{left:280px;top:2800px;width:620px;height:295px;background:#fafafa;box-shadow:0 4px 14px rgba(0,0,0,.12)}
.quote-card{left:251px;top:2768px;width:678px;height:300px;background:var(--white);box-shadow:0 6px 22px rgba(0,0,0,.14)}
.avatar{left:104px;top:48px;width:46px;height:46px;border-radius:50%;background:linear-gradient(135deg,#c89a82,#6d5a52)}
.q-name{left:169px;top:56px;font-family:"Poppins",sans-serif;font-weight:600;font-size:16px}
.q-role{left:169px;top:78px;font-size:11px;color:#555}
.q-text{left:103px;top:118px;width:450px;font-size:14px;line-height:24.5px;color:#666;font-style:italic;font-weight:300}
.stars{left:103px;top:198px;color:var(--gold);font-size:16px;letter-spacing:3px}
.sig{left:103px;top:230px;width:56px;height:16px;background:#d7d7d7;border-radius:3px}
.updown{width:40px;height:40px;border:2px solid var(--teal);border-radius:50%;display:flex;align-items:center;justify-content:center}

.contact-bg{left:0;top:3230px;width:1200px;height:880px;background:linear-gradient(90deg,#e6e6e6 0%,#f1f1f1 45%,#e9e9e9 100%)}
.contact-sub{left:0;width:1200px;top:3402px;text-align:center;font-size:18px;line-height:31px;color:#444}
.field{height:43px;border:1.5px solid #bfbfbf;border-radius:22px;font-size:12px;color:#888;padding:14px 18px;background:rgba(255,255,255,.35)}
.field.big{height:121px;border-radius:18px}

.footer-bg{left:0;top:3990px;width:1200px;height:658px;background:radial-gradient(ellipse at 50% 40%,#2a2d30 0%,#1a1c1e 70%)}
.f-logo{left:88px;top:4180px;font-size:50px;color:var(--white)}
.f-info{left:130px;font-size:16px;color:var(--white)}
.f-ic{left:94px;width:16px;height:16px;border:2px solid var(--white);border-radius:50%}
.f-head{font-family:"Poppins",sans-serif;font-weight:600;font-size:19px;color:var(--white);letter-spacing:.3px}
.f-text{left:527px;top:4256px;width:320px;font-size:13px;line-height:25px;color:var(--white)}
.f-input{left:527px;top:4323px;width:307px;height:35px;border-radius:18px;background:var(--white);font-size:10px;color:#777;padding:12px 16px}
.f-sub{left:527px;top:4378px;width:114px;height:34px;border-radius:17px;background:var(--teal);color:var(--white);font-size:12px;font-weight:700;display:flex;align-items:center;justify-content:center}
.f-links{left:962px;top:4242px;font-family:"Poppins",sans-serif;font-weight:500;font-size:17px;line-height:27.8px;color:var(--white)}
.f-rule{left:0;top:4484px;width:1200px;height:1px;background:rgba(255,255,255,.12)}
.copy{left:0;top:4516px;width:1200px;text-align:center;font-size:15px;color:var(--white)}
.f-social{width:32px;height:32px;border:1.5px solid var(--white);border-radius:50%;top:4559px}
</style>
</head>
<body>

<div class="abs topbar">
  <div class="abs contact-line"><span>&#9742; 555 014 2236 |</span><span>&#9993; info@lironvasek.com</span></div>
  <div class="abs social"><span class="dot"></span><span class="dot"></span><span class="dot"></span><span class="dot"></span></div>
</div>

<div class="abs logo serif">Liron Vasek</div>
<div class="abs call"><span class="ic"></span>Call Us: 555 014 2236</div>
<div class="abs btn-contact">CONTACT ME</div>
<div class="abs nav" style="left:469px">Home</div>
<div class="abs nav" style="left:565px">Portfolio</div>
<div class="abs nav" style="left:686px">Resume</div>
<div class="abs nav" style="left:801px">Achievements</div>
<div class="abs nav" style="left:964px">Blog</div>
<div class="abs nav" style="left:1043px">Contact</div>

<div class="abs hero-photo" role="img" aria-label="Smiling teenage student sitting at a laptop in a library"></div>
<div class="abs hero-shade"></div>
<svg class="abs" style="left:0;top:700px" width="1200" height="300" viewBox="0 0 1200 300">
  <path d="M0,22 C150,220 400,290 640,250 C850,215 1000,160 1200,200 L1200,300 L0,300 Z" fill="#fff"/>
  <path d="M0,22 C150,220 400,290 640,250 C850,215 1000,160 1200,200" fill="none" stroke="#0d5a63" stroke-width="12"/>
</svg>
<div class="abs hero-kicker serif">WELCOME TO</div>
<div class="abs hero-title serif">LIRON VASEK</div>
<div class="abs hero-text">Lorem Ipsum is simply dummy text of the printing and typesetting industry. Lorem Ipsum has been the industry's standard dummy text ever since the 1500s</div>
<div class="abs btn-ghost">Read More</div>
<div class="abs arrow" style="left:36px;top:478px"><svg width="14" height="14" viewBox="0 0 14 14"><path d="M9 2 L4 7 L9 12" fill="none" stroke="#fff" stroke-width="2"/></svg></div>
<div class="abs arrow" style="left:1133px;top:478px"><svg width="14" height="14" viewBox="0 0 14 14"><path d="M5 2 L10 7 L5 12" fill="none" stroke="#fff" stroke-width="2"/></svg></div>

<svg class="abs" style="left:80px;top:1060px" width="420" height="420" viewBox="0 0 420 420">
  <path d="M370,70 A200,200 0 1 0 200,410" fill="none" stroke="#0d5a63" stroke-width="10"/>
</svg>
<div class="abs about-photo" role="img" aria-label="Teenage boy with headphones giving a thumbs up"></div>
<div class="abs about-title serif">ABOUT ME</div>
<div class="abs about-text">Lorem Ipsum is simply dummy text of the printing and typesetting industry. Lorem Ipsum has been the industry's standard dummy text ever since the 1500s, when an unknown printer took a galley of type and scrambled it to make a type specimen book. It has survived not only five centuries, but also the leap into electronic typesetting, remaining essentially unchanged. It was popularised in the 1960s with the release of Letraset sheets containing Lorem Ipsum passages</div>
<div class="abs btn-solid" style="left:603px;top:1384px;width:167px;height:53px;font-size:19px">Read More</div>

<div class="abs dark-band" role="img" aria-label="Dimmed photo of students studying together"></div>
<svg class="abs" style="left:0;top:1540px" width="1200" height="300" viewBox="0 0 1200 300">
  <path d="M0,0 L1200,0 L1200,260 C1080,120 900,40 700,36 C450,32 250,110 0,80 Z" fill="#fff"/>
  <path d="M0,80 C250,110 450,32 700,36 C900,40 1080,120 1200,260" fill="none" stroke="#0d5a63" stroke-width="12"/>
</svg>
<svg class="abs" style="left:0;top:2300px" width="1200" height="300" viewBox="0 0 1200 300">
  <path d="M0,28 C120,190 320,260 560,260 C800,260 1000,175 1200,190 L1200,300 L0,300 Z" fill="#fff"/>
  <path d="M0,28 C120,190 320,260 560,260 C800,260 1000,175 1200,190" fill="none" stroke="#0d5a63" stroke-width="12"/>
</svg>

<div class="abs card" style="left:94px">
  <div class="ph" role="img" aria-label="Two friends laughing and celebrating at a phone" style="background:linear-gradient(120deg,#8a5a3c,#c97a4a 50%,#5b4436)"></div>
  <h3>ACCOMPLISHMENTS</h3>
  <p>Lorem Ipsum is simply dummy text of the printing and typesetting industry. Lorem Ipsum has been the industry</p>
</div>
<div class="abs card" style="left:433px">
  <div class="ph" role="img" aria-label="Interns working together around a table" style="background:linear-gradient(120deg,#d9d6cf,#6e7a72 50%,#2f3a36)"></div>
  <h3>INTERNSHIPS</h3>
  <p>Lorem Ipsum is simply dummy text of the printing and typesetting industry. Lorem Ipsum has been the industry</p>
</div>
<div class="abs card" style="left:772px">
  <div class="ph" role="img" aria-label="Volunteers planting trees in a park" style="background:linear-gradient(120deg,#b9c98f,#6f8a4e 50%,#4f5d3a)"></div>
  <h3>VOLUNTEER WORK</h3>
  <p>Lorem Ipsum is simply dummy text of the printing and typesetting industry. Lorem Ipsum has been the industry</p>
</div>
<div class="abs arrow" style="left:32px;top:2035px;width:48px;height:48px"><svg width="16" height="16" viewBox="0 0 14 14"><path d="M9 2 L4 7 L9 12" fill="none" stroke="#fff" stroke-width="2"/></svg></div>
<div class="abs arrow" style="left:1120px;top:2039px;width:48px;height:48px"><svg width="16" height="16" viewBox="0 0 14 14"><path d="M5 2 L10 7 L5 12" fill="none" stroke="#fff" stroke-width="2"/></svg></div>

<div class="abs section-title serif" style="top:2678px">TESTIMONIALS</div>
<div class="abs quote-back"></div>
<div class="abs quote-card">
  <div class="abs avatar" role="img" aria-label="Reviewer portrait"></div>
  <div class="abs q-name">DANA WHITCOMBE</div>
  <div class="abs q-role">CREATIVE DIRECTOR</div>
  <div class="abs q-text">It is a long established fact that a reader will be distracted readable content of a page when looking at its layout. The point of using rem Ipsum is that it has a look like readable English.</div>
  <div class="abs stars">&#9733;&#9733;&#9733;&#9733;&#9733;</div>
  <div class="abs sig" role="img" aria-label="Handwritten signature"></div>
</div>
<div class="abs updown" style="left:909px;top:2864px"><svg width="18" height="20" viewBox="0 0 18 20"><path d="M9 18 V3 M3 9 L9 3 L15 9" fill="none" stroke="#0d5a63" stroke-width="1.6"/></svg></div>
<div class="abs updown" style="left:909px;top:2934px"><svg width="18" height="20" viewBox="0 0 18 20"><path d="M9 2 V17 M3 11 L9 17 L15 11" fill="none" stroke="#0d5a63" stroke-width="1.6"/></svg></div>

<div class="abs contact-bg" role="img" aria-label="Faded photo of students on a campus"></div>
<div class="abs section-title serif" style="top:3326px">CONTACT ME</div>
<div class="abs contact-sub">Sed ut perspiciatis unde omnis iste natus error sit voluptatem<br>accusantium doloremque laudantium</div>
<div class="abs field" style="left:254px;top:3503px;width:332px">Your Name</div>
<div class="abs field" style="left:613px;top:3503px;width:331px">Your Email</div>
<div class="abs field" style="left:254px;top:3566px;width:332px">Your Phone</div>
<div class="abs field" style="left:613px;top:3566px;width:331px">Select Service</div>
<div class="abs field" style="left:254px;top:3629px;width:332px">Appointment Time</div>
<div class="abs field" style="left:613px;top:3629px;width:331px">Appointment Date</div>
<div class="abs field big" style="left:254px;top:3690px;width:690px">Your Comment</div>
<div class="abs btn-solid" style="left:449px;top:3844px;width:302px;height:50px;font-size:16px;font-family:'Poppins',sans-serif">Make an Appointment Now</div>

<div class="abs footer-bg" role="img" aria-label="Dark photo of a graduation crowd"></div>
<svg class="abs" style="left:0;top:3960px" width="1200" height="200" viewBox="0 0 1200 200">
  <path d="M0,0 L1200,0 L1200,175 C1100,80 950,30 800,36 C550,46 300,110 0,100 Z" fill="#eaeaea"/>
  <path d="M0,100 C300,110 550,46 800,36 C950,30 1100,80 1200,175" fill="none" stroke="#0d5a63" stroke-width="12"/>
</svg>
<div class="abs f-logo serif">LIRON VASEK</div>
<div class="abs f-ic" style="top:4270px"></div>
<div class="abs f-info" style="top:4258px;line-height:25px">219 Alder Row,<br>Maple Fork, MN 55012</div>
<div class="abs f-ic" style="top:4325px"></div>
<div class="abs f-info" style="top:4322px">Phone: 555 014 2236</div>
<div class="abs f-ic" style="top:4361px;border-radius:2px"></div>
<div class="abs f-info" style="top:4357px;line-height:31px">Email:<br>info@lironvasek.com</div>

<div class="abs f-head" style="left:527px;top:4200px">SIGN UP TO RECEIVE EMAIL</div>
<div class="abs f-text">Excepteur sint occaecat cupidatat non proident, sunt in culpa qui Nemo</div>
<div class="abs f-input">Enter Email</div>
<div class="abs f-sub">SUBSCRIBE</div>

<div class="abs f-head" style="left:962px;top:4198px">QUICK LINKS</div>
<div class="abs f-links">Home<br>Portfolio<br>Resume<br>Achievements<br>Blog<br>Contact Me</div>

<div class="abs f-rule"></div>
<div class="abs copy">&copy; 2019Copyrights | All Rights Reserved</div>
<div class="abs f-social" style="left:527px"></div>
<div class="abs f-social" style="left:563px"></div>
<div class="abs f-social" style="left:601px"></div>
<div class="abs f-social" style="left:637px"></div>

</body>
</html>
```